Corvin Ridge Software PowerPoint template

We are a software company selling endpoint visibility, access and security technology to enterprise-level IT departments.
Our technology helps organizations gain comprehensive visibility into and control over devices accessing their corporate network so they can quickly identify and address suspicious activity on the network that could lead to potential threats like data breaches.
This technology can cost organizations upwards of $1M - depending on the size of the organization. Our primary clients are Vestral 2,000 companies.
We want a professional, polished PowerPoint template that we can use for all company presentations. Please include:
Title page
Section page
General info page
Thank you page
Logo options and color specs are attached.
Please include our tagline on at least the title page: Discover the edge. Optimize the whole.
Reason: Seeking more options. Looking for a clean design that uses lots of white space.
Software

```html
<!DOCTYPE html>
<html lang="en">
<head>
<meta charset="utf-8">
<title>Corvin Ridge Software — Title Slide</title>
<link href="https://fonts.googleapis.com/css2?family=Exo+2:wght@300;400;600&display=swap" rel="stylesheet">
<style>
  :root {
    --brand-red: #8e1b21;
    --brand-copper: #c98a5e;
    --text-grey: #75787b;
    --rule-grey: #9a9a9a;
    --paper: #ffffff;
  }
  html, body {
    margin: 0;
    padding: 0;
    width: 1200px;
    height: 849px;
    overflow: hidden;
    background: var(--paper);
  }
  .slide {
    position: relative;
    width: 1200px;
    height: 849px;
    background: var(--paper);
    font-family: "Exo 2", "Helvetica Neue", Arial, sans-serif;
  }
  .tagline {
    position: absolute;
    left: 128px;
    top: 124px;
    margin: 0;
    font-weight: 300;
    font-size: 66px;
    line-height: 74px;
    letter-spacing: -0.5px;
    color: var(--brand-red);
    text-transform: uppercase;
  }
  .presentee {
    position: absolute;
    left: 130px;
    top: 308px;
    margin: 0;
    font-weight: 600;
    font-size: 22px;
    color: var(--text-grey);
    text-transform: uppercase;
  }
  .date {
    position: absolute;
    left: 130px;
    top: 344px;
    margin: 0;
    font-weight: 400;
    font-size: 20px;
    color: var(--text-grey);
    text-transform: uppercase;
  }
  .footer-rule {
    position: absolute;
    left: 131px;
    top: 731px;
    width: 544px;
    height: 1px;
    background: var(--rule-grey);
  }
  .website {
    position: absolute;
    left: 131px;
    top: 749px;
    margin: 0;
    font-weight: 400;
    font-size: 15px;
    color: var(--brand-red);
    text-transform: uppercase;
  }
  .wordmark {
    position: absolute;
    left: 710px;
    top: 690px;
    display: flex;
    align-items: center;
    gap: 22px;
  }
  .wordmark-mark {
    width: 58px;
    height: 58px;
    background: var(--brand-copper);
  }
  .wordmark-name {
    font-weight: 600;
    font-size: 34px;
    letter-spacing: 3px;
    color: var(--brand-red);
    text-transform: uppercase;
    line-height: 1.1;
  }
</style>
</head>
<body>
  <main class="slide">
    <h1 class="tagline">Discover the edge,<br>Optimize the whole</h1>
    <p class="presentee">Name of the presentee</p>
    <p class="date">Date : MM DD YY</p>

    <div class="footer-rule"></div>
    <p class="website">www.corvinridgesoftware.com</p>

    <div class="wordmark">
      <div class="wordmark-mark"></div>
      <div class="wordmark-name">Corvin Ridge<br>Software</div>
    </div>
  </main>
</body>
</html>
```